Design website for new email startup

We are starting a company called Pingo.QZ (it will live at http://pingo.qz).

We would like the main landing page for our site designed. We have provided a very simple wireframe to help provide direction for the content it should include, but we do not expect the designers to adhere to it at all - we encourage unique ideas. There is some sample text in the wireframe - this does not have to be used, but may provide ideas.

We provide an easy way for people to manage email for a custom domain name. For example if you own "yourhouseword.example" you can point your DNS records to us and we'll make it easy to have emails addressed to your domain get forwarded to your existing email (gmail, etc). Folks running blogs, and other small sites can quickly setup email addresses for their domains and manage them in one place.

(For technical folks, we have you point your dns mx records to us, hence the name. That way all your email hits us and we can redirect it wherever you want. We make it easy to manage a single domain or a bunch of domains. Many domain registrars offer this service for a fee, and have clumsy management tools. We provide a robust simple toolset for free, as well as premium options).

The goal of the landing page is to get folks into the signup flow. The second priority flow is to have them take a look at the premium plan offerings.

We may offer the winning designer additional work for the remainder of the site design.
Updates

I've changed this project to a committed payment.  It is no longer refundable.  Thank you.

Target Market(s)

Bloggers, podcasters, designers, app developers - people who are a little tech savvy.

Industry/Entity Type

It Company

Font styles to use
Sans Serif

Colors

Designer to choose colors to be used in the design.

Requirements
Must have
• A full fidelity mockup (comp) of the landing page including the source file (psd, ai, etc).

Some sort of logo treatment for the pingo.qz brand

A call to action for signup, such as the suggested 'Get Started Here'
Nice to have
• A hip startup feel

Incorporation of the email theme

Give the impression it is simple, easy and fast

```html
<!DOCTYPE html>
<html lang="en">
<head>
<meta charset="utf-8">
<title>Pingo.QZ — We make Email easy</title>
<link rel="stylesheet" href="https://fonts.googleapis.com/css2?family=Signika:wght@300;400;600&display=swap">
<style>
  :root {
    --brand-orange: #f7a51c;
    --brand-orange-dark: #e08f0a;
    --header-bg: #232323;
    --footer-bg: #2b2b2b;
    --ink: #2f2f2f;
    --ink-soft: #777777;
    --card-bg: #f3f2f3;
    --card-border: #c9c9c9;
    --button-dark: #333333;
    --white: #ffffff;
    --footer-text: #d0d0d0;
    --icon-grey: #7a7a7a;
  }
  * { margin: 0; padding: 0; box-sizing: border-box; }
  html, body { width: 1200px; height: 949px; overflow: hidden; }
  body {
    position: relative;
    background: var(--white);
    font-family: "Signika", "Trebuchet MS", sans-serif;
    color: var(--ink);
  }

  /* Header */
  .site-header {
    position: absolute; left: 0; top: 0; width: 1200px; height: 111px;
    background:
      repeating-linear-gradient(90deg, rgba(255,255,255,0.025) 0 1px, transparent 1px 3px),
      repeating-linear-gradient(0deg, rgba(255,255,255,0.02) 0 1px, transparent 1px 3px),
      var(--header-bg);
  }
  .brand {
    position: absolute; left: 131px; top: 32px;
    font-size: 47px; font-weight: 300; letter-spacing: 1px; line-height: 1;
    color: var(--brand-orange);
  }
  .main-nav {
    position: absolute; right: 136px; top: 68px;
    display: flex; font-size: 15px; color: var(--white);
  }
  .main-nav a { color: var(--white); text-decoration: none; }
  .main-nav .divider { margin: 0 26px; }

  /* Hero */
  .hero {
    position: absolute; left: 0; top: 111px; width: 1200px; height: 416px;
  }
  .hero-photo {
    position: absolute; inset: 0;
    background: linear-gradient(90deg, #e9ebed 0%, #f2f3f4 25%, #eceded 45%, #d8d6d4 60%, #b9b5b2 75%, #cfcbc7 88%, #9a9897 100%);
  }
  .benefits {
    position: absolute; left: 137px; top: 85px; width: 470px;
    list-style: none; font-size: 20px; line-height: 24px; color: var(--ink);
  }
  .benefits li { position: relative; padding-left: 35px; margin-bottom: 11px; }
  .benefits svg { position: absolute; left: 0; top: 3px; }
  .cta {
    position: absolute; top: 316px; height: 42px; width: 161px;
    display: flex; align-items: center; justify-content: center;
    font-size: 14px; text-transform: uppercase; text-decoration: none;
    box-shadow: 0 1px 2px rgba(0,0,0,0.25);
  }
  .cta-primary { left: 137px; background: var(--brand-orange); color: #3a2a05; }
  .cta-secondary { left: 328px; background: var(--button-dark); color: var(--white); height: 43px; }

  /* Guide cards */
  .guide-card {
    position: absolute; top: 572px; width: 460px; height: 235px;
    background: var(--card-bg);
  }
  .guide-card.first { left: 130px; }
  .guide-card.second { left: 609px; }
  .partner-box {
    position: absolute; left: 17px; top: 25px; width: 176px; height: 137px;
    background: var(--white); border: 1px solid var(--card-border);
    display: flex; align-items: center; justify-content: center;
    font-size: 24px; font-weight: 400; color: var(--ink);
  }
  .second .partner-box { top: 28px; }
  .guide-title {
    position: absolute; left: 215px; top: 24px; width: 235px;
    font-size: 16px; font-weight: 400; line-height: 21px; color: var(--ink);
  }
  .guide-intro {
    position: absolute; left: 217px; top: 88px; width: 225px;
    font-size: 13px; line-height: 20px; color: var(--ink-soft);
  }
  .guide-more {
    position: absolute; left: 17px; top: 172px; width: 430px;
    font-size: 13px; line-height: 20px; color: var(--ink-soft);
  }
  .second .guide-intro { top: 87px; }
  .second .guide-more { left: 21px; top: 175px; }

  /* Footer */
  .site-footer {
    position: absolute; left: 0; top: 856px; width: 1200px; height: 93px;
    background: var(--footer-bg);
  }
  .copyright {
    position: absolute; left: 132px; top: 31px;
    font-size: 14px; color: var(--footer-text);
  }
  .social { position: absolute; left: 937px; top: 31px; display: flex; gap: 9px; }
</style>
</head>
<body>

<header class="site-header">
  <div class="brand">PINGO.QZ</div>
  <nav class="main-nav">
    <a href="#">How it works</a><span class="divider">|</span>
    <a href="#">Support</a><span class="divider">|</span>
    <a href="#">Login</a>
  </nav>
</header>

<section class="hero">
  <div class="hero-photo" role="img" aria-label="Photo of a smiling woman at a computer with a colleague leaning over her shoulder in a bright office"></div>
  <ul class="benefits">
    <li><svg width="18" height="16" viewBox="0 0 18 16"><rect x="0.5" y="2.5" width="13" height="13" fill="none" stroke="#f7a51c" stroke-width="1.5"/><path d="M3 8 L7 12 L17 1" fill="none" stroke="#f7a51c" stroke-width="2.5"/></svg>We make Email easy.</li>
    <li><svg width="18" height="16" viewBox="0 0 18 16"><rect x="0.5" y="2.5" width="13" height="13" fill="none" stroke="#f7a51c" stroke-width="1.5"/><path d="M3 8 L7 12 L17 1" fill="none" stroke="#f7a51c" stroke-width="2.5"/></svg>Give us five min &amp; we’ll get you Email from your domain.</li>
    <li><svg width="18" height="16" viewBox="0 0 18 16"><rect x="0.5" y="2.5" width="13" height="13" fill="none" stroke="#f7a51c" stroke-width="1.5"/><path d="M3 8 L7 12 L17 1" fill="none" stroke="#f7a51c" stroke-width="2.5"/></svg>Easily forward mail from your custom domain name wherever you want it.</li>
    <li><svg width="18" height="16" viewBox="0 0 18 16"><rect x="0.5" y="2.5" width="13" height="13" fill="none" stroke="#f7a51c" stroke-width="1.5"/><path d="M3 8 L7 12 L17 1" fill="none" stroke="#f7a51c" stroke-width="2.5"/></svg>You take the mail, we’ll keep the spam.</li>
  </ul>
  <a class="cta cta-primary" href="#">Get started here</a>
  <a class="cta cta-secondary" href="#">Compare plans</a>
</section>

<article class="guide-card first">
  <div class="partner-box">SkyRelay</div>
  <h2 class="guide-title">How to configure your SkyRelay DNS to use pingo.qz</h2>
  <p class="guide-intro">Sed ut perspiciatis unde omnis iste natus error sit voluptatem accusan­tium doloremque laudantium, totam­rem aperiam, eaque ipsa</p>
  <p class="guide-more">quae ab illo inventore veritatis et quasi architecto beatae vitae dictaesi sunt explicabo</p>
</article>

<article class="guide-card second">
  <div class="partner-box">NameHarbor</div>
  <h2 class="guide-title">Use pingo.qz with your NameHarbor domain registration.</h2>
  <p class="guide-intro">Sed ut perspiciatis unde omnis iste natus error sit voluptatem accusan­tium doloremque laudantium, totam­rem aperiam, eaque ipsa</p>
  <p class="guide-more">quae ab illo inventore veritatis et quasi architecto beatae vitae dictaesi sunt explicabo</p>
</article>

<footer class="site-footer">
  <p class="copyright">Copyright (c) 2014. pingo.qz . All right reserved.</p>
  <div class="social">
    <svg width="25" height="25" viewBox="0 0 25 25" aria-label="Social profile"><circle cx="12.5" cy="12.5" r="12" fill="#7a7a7a"/></svg>
    <svg width="25" height="25" viewBox="0 0 25 25" aria-label="Social profile"><circle cx="12.5" cy="12.5" r="12" fill="#7a7a7a"/></svg>
    <svg width="25" height="25" viewBox="0 0 25 25" aria-label="Social profile"><circle cx="12.5" cy="12.5" r="12" fill="#7a7a7a"/></svg>
    <svg width="25" height="25" viewBox="0 0 25 25" aria-label="Email"><circle cx="12.5" cy="12.5" r="12" fill="#7a7a7a"/><rect x="6.5" y="8.5" width="12" height="8" fill="none" stroke="#2b2b2b" stroke-width="1.3"/><path d="M6.5 8.5 L12.5 13 L18.5 8.5" fill="none" stroke="#2b2b2b" stroke-width="1.3"/></svg>
  </div>
</footer>

</body>
</html>
```